body therapist

I need to offer my services as a massage therapist at home, acclimating customer space aroma candles with music and everything else to bring comfort. 8 offer rituals like this: relaxing ritual, purifying ritual, ritual breast, facial and body cleansing ritual organic, ritual man, ritual feet, slimming ritual. Naraja handling colors, seawater, green, lavender

Target Market(s)

men and women, tired, stressed, looking for something new

Font styles to use
Decorative
Script

Colors
f37122
0493ce
abd037

Requirements
Must have
• detailing each massage
Nice to have
• simple and elegant

```html
<!DOCTYPE html>
<html lang="es">
<head>
<meta charset="utf-8">
<title>Serenia Spa — Nuevos Rituales de relajación</title>
<link rel="stylesheet" href="https://fonts.googleapis.com/css2?family=Arvo&family=Lobster&display=swap">
<style>
  :root {
    --stage: #3c3c3c;
    --paper: #ececec;
    --lime: #abd037;
    --lime-light: #c4e25a;
    --lime-deep: #5f8f1c;
    --orange: #f37122;
    --orange-light: #f79a5e;
    --sea: #0493ce;
    --white: #ffffff;
    --slab: "Arvo", Georgia, serif;
    --script: "Lobster", cursive;
  }
  * { box-sizing: border-box; margin: 0; padding: 0; }
  html, body { width: 1200px; height: 1200px; overflow: hidden; }
  body {
    background: var(--stage);
    position: relative;
    font-family: var(--slab);
    color: var(--white);
  }
  .cover {
    position: absolute;
    top: 240px;
    width: 540px;
    height: 720px;
    background: var(--paper);
    overflow: hidden;
  }
  .cover--back { left: 40px; }
  .cover--front { left: 620px; }

  .photo { position: absolute; left: 0; top: 0; width: 100%; }
  .photo--bamboo {
    height: 270px;
    background: linear-gradient(100deg, #2f6b14 0%, #5fa62a 35%, #3d7d1a 60%, #8f9a86 80%, #4f8a22 100%);
  }
  .photo--seashore {
    height: 290px;
    background: linear-gradient(180deg, #b9d3e4 0%, #8fb6cf 35%, #2d7fa8 60%, #d9e6ea 78%, #3a86ad 100%);
  }

  .water-panel {
    position: absolute;
    right: 22px;
    background:
      radial-gradient(ellipse 70% 45% at 55% 72%, #2f6a12 0%, rgba(47,106,18,0) 70%),
      linear-gradient(170deg, var(--lime-light) 0%, var(--lime) 40%, #8fbf2c 70%, var(--lime-deep) 100%);
  }
  .cover--front .water-panel { left: 100px; top: 205px; bottom: 130px; }
  .cover--back .water-panel { left: 80px; top: 250px; bottom: 110px; }

  .band {
    position: absolute;
    left: 0; right: 0; bottom: 0;
    background: linear-gradient(100deg, var(--orange-light) 0%, var(--orange) 30%, var(--orange) 100%);
  }
  .cover--front .band { height: 130px; }
  .cover--back .band { height: 110px; display: flex; align-items: center; justify-content: flex-end; padding-right: 40px; }
  .band__tagline { font-size: 24px; }

  .headline {
    position: absolute;
    left: 118px;
    top: 262px;
    font-size: 76px;
    font-weight: 400;
    line-height: 1;
    white-space: nowrap;
  }
  .intro {
    position: absolute;
    left: 150px;
    top: 360px;
    font-size: 28px;
    line-height: 1.05;
  }
  .brand {
    font-family: var(--script);
    font-weight: 400;
    line-height: 1;
  }
  .cover--front .brand { position: absolute; left: 150px; top: 468px; font-size: 44px; }
  .ritual-note {
    position: absolute;
    left: 150px;
    top: 530px;
    font-family: var(--script);
    font-size: 26px;
    white-space: nowrap;
  }

  .contact-card { position: absolute; left: 120px; top: 300px; }
  .contact-card .brand { font-size: 58px; margin-bottom: 18px; }
  .contact-card__label {
    font-size: 15px;
    text-decoration: underline;
    margin-bottom: 6px;
  }
  .contact-line {
    display: flex;
    align-items: center;
    gap: 10px;
    font-size: 17px;
    margin-bottom: 8px;
    letter-spacing: 0.5px;
  }
  .contact-line svg { width: 20px; height: 20px; flex: none; }
  .social-handle {
    display: flex;
    align-items: center;
    gap: 10px;
    margin-top: 14px;
    font-size: 18px;
  }
  .social-handle__dot { width: 14px; height: 14px; background: var(--white); }
</style>
</head>
<body>

  <section class="cover cover--back" aria-label="Contraportada">
    <div class="photo photo--seashore" role="img" aria-label="Fotografía de una mujer de espaldas con los brazos abiertos frente al mar y gaviotas volando"></div>
    <div class="water-panel" role="img" aria-label="Fondo fotográfico de agua verde con ondas"></div>
    <div class="contact-card">
      <p class="brand">Serenia Spa</p>
      <p class="contact-card__label">CONTACTO:</p>
      <p class="contact-line">
        <svg viewBox="0 0 20 20" aria-hidden="true"><rect x="2" y="4" width="16" height="12" fill="none" stroke="#fff" stroke-width="1.6"/><path d="M2 4 L10 11 L18 4" fill="none" stroke="#fff" stroke-width="1.6"/></svg>
        HOLA@SERENIA-SPA.CO
      </p>
      <p class="contact-line">
        <svg viewBox="0 0 20 20" aria-hidden="true"><path d="M5 2 L8 2 L9 6 L7 8 Q9 12 12 13 L14 11 L18 12 L18 15 Q17 18 14 18 Q4 16 2 6 Q2 3 5 2 Z" fill="#fff"/></svg>
        TEL + 57 310 555 0192
      </p>
      <p class="social-handle"><span class="social-handle__dot"></span>@serenia.spa</p>
    </div>
    <div class="band"><p class="band__tagline">Nuevos Rituales de relajación</p></div>
  </section>

  <section class="cover cover--front" aria-label="Portada">
    <div class="photo photo--bamboo" role="img" aria-label="Fotografía de bambú verde con una torre de piedras apiladas"></div>
    <div class="water-panel" role="img" aria-label="Fondo fotográfico de agua verde con ondas"></div>
    <h1 class="headline">Explorar</h1>
    <p class="intro">Nuevos<br>Rituales de<br>relajación con</p>
    <p class="brand">Serenia Spa</p>
    <p class="ritual-note">con velas aromáticas y música</p>
    <div class="band"></div>
  </section>

</body>
</html>
```